Label or packaging Design for Hair Care Line

Dear Designer,
We are Pelvoro, a brand known for our premium hairstyling tools, and we are excited to expand into hair care. We are currently looking for a talented designer to create the label designs for our entire luxury hair care line.
This project is crucial in establishing our visual identity in the hair care market, and we aim to position ourselves alongside premium brands such as TKW, Fendrick Hair Atelier, and Morvi.
Project Scope
We need a cohesive label design for our hair care line, which includes:
5 products (e.g., shampoo, conditioner, hair oil, styling cream, and a hair mask).
The designs should include:
Front label: Highlighting the product name, key features, and branding.
Our goal is to achieve a design that communicates premium luxury with a touch of professionalism. Below are the specific guidelines to help you align with our vision:
Style and Inspiration
Think of brands like TKW, Fendrick Hair Atelier, and Morvi.
Luxury and Minimalism: Clean lines, sophisticated typography, and an elegant color palette.
Subtle femininity: premium finishes like metallic accents (gold, silver, or rose gold).
Brand Personality
Premium: Reflecting high quality and exclusivity.
Modern & Professional: Appealing to a refined, professional audience but also suitable for lifestyle-oriented customers.
Warm & Empowering: A brand that celebrates confidence and individuality.
Color Palette
Neutral tones like black, white, accented with metallics (gold or silver) for a luxurious feel.
Colors that feel timeless and elegant rather than trendy or overly bright.
Typography
Use clean, modern fonts (preferably sans-serif or serif for a refined look).
Clear and legible for all product details while maintaining a high-end aesthetic.
Materials and Finishes
Packaging Shape
The label designs should suit a variety of bottle and jar shapes (e.g., cylindrical, flat, or rounded).
Keep scalability in mind so the identity remains consistent across different products.
Deliverables
To understand the aesthetic we are aiming for, here are some brands to use as inspiration:
TKW: For its minimalistic and modern approach.
Fendrick Hair Atelier: For its combination of luxury and professional appeal.
Morvi: For its soft femininity and lifestyle branding.
we would like to see your designs applied to a variety of packaging types to get an overall impression of how the brand identity works across different product formats. This includes:
A squeeze bottle (e.g., for styling creams or conditioners).
A glass bottle with a dropper (e.g., for a luxurious hair oil).
A shampoo/conditioner bottle (standard pump or flip-top cap).
A spray bottle (e.g., for leave-in treatments or heat protectors).
By creating designs for these different packaging types, we can better evaluate how cohesive and versatile the brand identity will be across the entire product line.

Updates
As you may have noticed from the designs, they don’t quite align with our briefing. The look needs to be clean and professional, similar to Fendrick, TKW, and the other examples we provided. Please address this, and we’ll check it!

Target Market(s)
europe and us
Font styles to use
Other font styles liked:
- century gothic

Look and feel

```html
<!DOCTYPE html>
<html lang="en">
<head>
<meta charset="UTF-8">
<title>Pelvoro Conditioner – Front Label</title>
<link href="https://fonts.googleapis.com/css2?family=Questrial&family=Outfit:wght@400;500&display=swap" rel="stylesheet">
<style>
  :root {
    --backdrop: #e6e6e6;
    --label: #f7f7f7;
    --ink: #3f3f3f;
    --ink-soft: #555555;
    --rose-gold: #c99a82;
    --rose-gold-light: #ead6cb;
  }
  * { margin: 0; padding: 0; box-sizing: border-box; }
  html, body {
    width: 1200px;
    height: 1200px;
    overflow: hidden;
    background: var(--backdrop);
  }
  .canvas {
    position: relative;
    width: 1200px;
    height: 1200px;
    display: flex;
    align-items: center;
    justify-content: center;
  }
  .label {
    position: relative;
    width: 600px;
    height: 1100px;
    background: var(--label);
    border-radius: 6px;
  }
  .brand-name {
    position: absolute;
    left: 330px;
    top: 330px;
    transform: translate(-50%, -50%) rotate(-90deg);
    font-family: "Questrial", "Century Gothic", sans-serif;
    font-size: 150px;
    line-height: 1;
    color: var(--ink);
    white-space: nowrap;
    letter-spacing: -0.01em;
  }
  .product-name {
    position: absolute;
    top: 665px;
    left: 0;
    width: 100%;
    text-align: center;
    font-family: "Outfit", "Century Gothic", sans-serif;
    font-weight: 500;
    font-size: 22px;
    letter-spacing: 0.42em;
    padding-left: 0.42em;
    color: var(--ink);
  }
  .ingredient-emblem {
    position: absolute;
    top: 730px;
    left: 50%;
    width: 120px;
    height: 120px;
    transform: translateX(-50%);
    border-radius: 50%;
    background: radial-gradient(circle, var(--label) 30%, var(--rose-gold-light) 62%, var(--label) 72%);
  }
  .description {
    position: absolute;
    top: 900px;
    left: 50%;
    width: 300px;
    transform: translateX(-50%);
    text-align: center;
    font-family: "Outfit", sans-serif;
    font-size: 11.5px;
    line-height: 1.25;
    color: var(--ink-soft);
  }
  .volume {
    position: absolute;
    top: 1010px;
    left: 0;
    width: 100%;
    text-align: center;
    font-family: "Outfit", sans-serif;
    font-size: 17px;
    color: var(--ink);
  }
</style>
</head>
<body>
  <main class="canvas">
    <section class="label">
      <h1 class="brand-name">Pelvoro</h1>
      <h2 class="product-name">CONDITIONER</h2>
      <div class="ingredient-emblem" role="img" aria-label="Rose-gold ring of almond leaf motifs"></div>
      <p class="description">Lorem ipsum dolor sit amet, consectetur adipiscing elit, sed do eiusmod tempor incididunt ut labore et dolore magna aliqua Ut enim ad minim veniam, quis tui estre efit nostrud exercitation.</p>
      <p class="volume">100ml&#8494;</p>
    </section>
  </main>
</body>
</html>
```